Law Firm Logo and Business Card Design

I need a logo and business card design for a law firm I just started. The law firm is named Law Office of Doreen K. Ashworth, LLC. The type of law I practice is Family Law, which includes divorce, custody, child support, alimony, property division, and the like. I would like to see designs that are unique and modern, yet sophisticated. I would also like to use the logo/design for my letterhead. I am not opposed to using some form of the scales of justice although I'd like something other than the typical, old fashioned scales of justice. I had considered a house made out of puzzle pieces with one puzzle piece pulled away from the others, with the logo text reading "Steady guidance for every family, one step at a time." However, I don't want that particular design to look juvenile. I also would not be opposed to some form of my initials on the logo -- my initials are DKA. I am open to any other ideas you may have. I would like to see raised designs/lettering, and/or metallic finish. I like the colors black, white, gold, silver, and/or teal.

Industry/Entity Type

Law Firm

```html
<!DOCTYPE html>
<html lang="en">
<head>
<meta charset="utf-8">
<title>Law Office of Doreen K. Ashworth, LLC — Business Card</title>
<link rel="stylesheet" href="https://fonts.googleapis.com/css2?family=Open+Sans:wght@400;700&family=Archivo+Narrow:ital@1&display=swap">
<style>
  :root {
    --canvas-bg: #e4e4e4;
    --card-front: #c9cacc;
    --card-back: #ffffff;
    --teal: #1b7a7e;
    --gold: #c9a75e;
    --ink: #1a1a1a;
    --text-grey: #3a3a3a;
    --faint: #d2d2d2;
    --rule: #5a5a5a;
  }
  html, body {
    margin: 0;
    width: 1200px;
    height: 900px;
    overflow: hidden;
    background: var(--canvas-bg);
    font-family: "Open Sans", Arial, sans-serif;
  }
  .card-set {
    display: flex;
    gap: 60px;
    justify-content: center;
    align-items: center;
    height: 100%;
  }
  .card {
    width: 525px;
    height: 300px;
    position: relative;
    box-shadow: 0 6px 18px rgba(0,0,0,0.12);
    box-sizing: border-box;
  }
  .card--front {
    background: var(--card-front);
    display: flex;
    flex-direction: column;
    align-items: center;
    padding-top: 48px;
  }
  .brand-mark {
    display: flex;
    align-items: center;
    gap: 10px;
    color: var(--teal);
    font-weight: 700;
    font-size: 34px;
    letter-spacing: 2px;
  }
  .brand-mark__dot {
    width: 26px;
    height: 26px;
    border-radius: 50%;
    background: var(--gold);
  }
  .tagline {
    margin: 14px 0 0;
    font-family: "Archivo Narrow", "Arial Narrow", sans-serif;
    font-style: italic;
    font-size: 12px;
    color: var(--text-grey);
  }
  .firm-name {
    margin: 12px 0 0;
    color: var(--teal);
    font-weight: 700;
    font-size: 27px;
    line-height: 1.15;
    text-align: center;
  }
  .card--back {
    background: var(--card-back);
    padding: 34px 40px;
  }
  .back-name {
    margin: 0;
    font-weight: 700;
    font-size: 19px;
    line-height: 1.2;
    color: var(--ink);
    width: 330px;
    padding-bottom: 12px;
    border-bottom: 1px solid var(--rule);
  }
  .contact-list {
    list-style: none;
    margin: 14px 0 0;
    padding: 0;
    font-size: 14px;
    line-height: 1.7;
    color: var(--ink);
  }
  .back-mark {
    position: absolute;
    top: 40px;
    right: 40px;
    display: flex;
    align-items: center;
    gap: 8px;
    color: var(--faint);
    font-weight: 700;
    font-size: 26px;
    letter-spacing: 2px;
  }
  .back-mark__dot {
    width: 20px;
    height: 20px;
    border-radius: 50%;
    background: var(--faint);
  }
</style>
</head>
<body>
  <main class="card-set">
    <section class="card card--front" aria-label="Business card front">
      <div class="brand-mark"><span class="brand-mark__dot"></span>DKA</div>
      <p class="tagline">"Steady guidance for every family, one step at a time."</p>
      <h1 class="firm-name">Law Office of<br>Doreen K. Ashworth, LLC.</h1>
    </section>

    <section class="card card--back" aria-label="Business card back">
      <h2 class="back-name">Law Office of<br>Doreen K. Ashworth, LLC.</h2>
      <div class="back-mark"><span class="back-mark__dot"></span>DKA</div>
      <ul class="contact-list">
        <li>(555) 014-2290</li>
        <li>info@ashworthfamilylaw.com</li>
        <li>www.ashworthfamilylaw.com</li>
      </ul>
    </section>
  </main>
</body>
</html>
```